Velvet Glow Co. Derma Roller packaging design

I need a box designed for a skin care brand called Velvet Glow Co. The box will be for our Derma Roller- a skin rejuvenation device. It will be sold online with lots of competition. I would like a modern, high end design, something that stands out and looks amazing. My logo is blush pink and black, for packaging i need no more than 3 colours, maybe gold if any other colour is used. A photo of a sample derma roller is attached below for an idea of what the product looks like, however my roller with have a clear handle with a black roller. The roller comes in a clear case, the box dimensions will need to be 16 cm long, 4 cm high, 4.5 cm wide.
ATTACHED ARE 2 SAMPLE BOXES AS AN EXAMPLE OF THE SIZE OF BOX REQUIRED!

Target Market(s)

25-50 year old women in the US

Colors
e667a6
000000
efefef

Requirements
Must have
• LOGO
• NAME OF PRODUCT- Cosmetic Derma Roller
• NEEDLE DEPTH- 0.25mm
• CAUTION- For personal use only, Do not use if allergic to metal, Do not use on open skin, wounds or active acne, sterilise roller before and after use.
Nice to have
• BENEFITS- Skin Rejuvenation, Collagen Induction Therapy, Increase product absorption, reduce acne scars and pigmentation
• FEATURES- 540 high quality titanium needles, ultra sharp needle tips, cross-line needle arrangement, ergonomic handle, anti slip grip,

```html
<!DOCTYPE html>
<html lang="en">
<head>
<meta charset="UTF-8">
<title>Velvet Glow Co. – Cosmetic Derma Roller Packaging</title>
<link href="https://fonts.googleapis.com/css2?family=Oswald:wght@400;500&display=swap" rel="stylesheet">
<style>
  :root {
    --page-bg: #fbf6f5;
    --pink-deep: #b8568a;
    --pink-mid: #db82ad;
    --pink-light: #f3bdd6;
    --pink-mist: #f7cfe0;
    --rose-gold: #cf9c86;
    --rose-gold-dark: #b98370;
    --label-white: #ffffff;
    --ink: #1c1c1c;
  }
  * { box-sizing: border-box; margin: 0; padding: 0; }
  html, body {
    width: 1200px;
    height: 1200px;
    overflow: hidden;
    background: var(--page-bg);
    font-family: "Oswald", "Arial Narrow", sans-serif;
  }
  .canvas {
    position: relative;
    width: 1200px;
    height: 1200px;
  }
  .box-panel {
    position: absolute;
    top: 62px;
    width: 400px;
    height: 1076px;
    box-shadow: 0 4px 14px rgba(120, 70, 80, 0.22);
    overflow: hidden;
  }
  .box-panel--front { left: 134px; }
  .box-panel--back { left: 666px; }

  .foliage-pattern {
    position: absolute;
    inset: 0;
    background:
      radial-gradient(ellipse 60% 30% at 30% 18%, var(--pink-mid) 0%, transparent 70%),
      radial-gradient(ellipse 55% 25% at 75% 80%, var(--pink-deep) 0%, transparent 70%),
      radial-gradient(ellipse 50% 25% at 20% 85%, var(--pink-light) 0%, transparent 75%),
      linear-gradient(180deg, var(--pink-mid) 0%, var(--pink-light) 35%, var(--pink-mist) 50%, var(--pink-light) 70%, var(--pink-mid) 100%);
  }

  .label-card {
    position: absolute;
    left: 24px;
    top: 358px;
    width: 355px;
    height: 358px;
    background: var(--label-white);
    border: 6px solid var(--rose-gold);
  }

  .brand-mark {
    position: absolute;
    left: 0;
    right: 0;
    top: 92px;
    display: flex;
    align-items: center;
    justify-content: center;
    gap: 10px;
  }
  .brand-mark__square {
    width: 14px;
    height: 14px;
    background: var(--pink-light);
  }
  .brand-mark__name {
    font-family: "Oswald", "Arial Narrow", sans-serif;
    font-weight: 400;
    font-size: 30px;
    letter-spacing: 2px;
    color: var(--ink);
    text-transform: uppercase;
  }

  .product-title {
    font-family: "Oswald", "Arial Narrow", sans-serif;
    font-weight: 400;
    font-size: 23px;
    letter-spacing: 0.5px;
    color: var(--rose-gold);
    text-transform: uppercase;
    text-align: center;
  }
  .label-card--front .product-title {
    position: absolute;
    left: 0;
    right: 0;
    top: 238px;
  }
  .label-card--back .product-title {
    margin-top: 48px;
  }

  .product-details {
    padding: 0 18px 0 36px;
    margin-top: 22px;
  }
  .product-details p {
    font-size: 11.6px;
    line-height: 19.5px;
    color: var(--ink);
    text-transform: uppercase;
    margin-bottom: 19px;
    letter-spacing: 0.1px;
  }
</style>
</head>
<body>
<div class="canvas">

  <section class="box-panel box-panel--front">
    <div class="foliage-pattern" role="img" aria-label="Pink metallic foil tropical leaf pattern with palm and monstera silhouettes"></div>
    <div class="label-card label-card--front">
      <div class="brand-mark">
        <span class="brand-mark__square"></span>
        <span class="brand-mark__name">Velvet Glow Co.</span>
      </div>
      <h1 class="product-title">Cosmetic Derma Roller</h1>
    </div>
  </section>

  <section class="box-panel box-panel--back">
    <div class="foliage-pattern" role="img" aria-label="Pink metallic foil tropical leaf pattern with palm and monstera silhouettes"></div>
    <div class="label-card label-card--back">
      <h2 class="product-title">Cosmetic Derma Roller</h2>
      <div class="product-details">
        <p>Benefits: Skin rejuvenation, collagen induction therapy, increase product absorption, reduce acne scars and pigmentation</p>
        <p>Features: 540 high quality 0.25 mm titanium needles, ultra sharp needle tips, cross-line needle arrangement, ergonomic handle, anti slip grip</p>
        <p>Caution: For personal use only, do not use if allergic to metal, do not use on open skin, wounds or active acne, sterilise roller before and after use.</p>
      </div>
    </div>
  </section>

</div>
</body>
</html>
```